Design a New Business Card for Our Company

We are looking for fresh, unique, and a modern business card that reflects our roots as digital marketing agency focused on SEM.

Industry/Entity Type

Marketing

Contact Information for Business Card

looking for very unique out of the box designs. clean and modern that compliments our logo

Requirements
Must have
• colors should match our logo
• Front should have name, address, email, and phone/fax of the person, phone/fax are the same number
• back should have our url

```html
<!DOCTYPE html>
<html lang="en">
<head>
<meta charset="utf-8">
<title>Brightwave Digital – Business Card</title>
<link rel="stylesheet" href="https://fonts.googleapis.com/css2?family=Arimo:wght@400;700&display=swap">
<style>
  :root {
    --backdrop: #e6e4e1;
    --card: #1d1d1f;
    --card-edge: #2a2a2d;
    --brand-blue: #4a8fd8;
    --text-light: #d6d6d6;
    --text-muted: #a9a9ab;
    --divider: #6a6a6e;
  }
  * { box-sizing: border-box; margin: 0; padding: 0; }
  html, body {
    width: 1200px; height: 787px; overflow: hidden;
    background: var(--backdrop);
    font-family: "Arimo", Arial, sans-serif;
  }
  .canvas {
    width: 1200px; height: 787px;
    display: flex; align-items: center; justify-content: center; gap: 40px;
  }
  .card {
    position: relative;
    width: 560px; height: 320px;
    background: var(--card);
    border: 1px solid var(--card-edge);
    box-shadow: 0 8px 24px rgba(0,0,0,0.18);
  }
  .brand {
    display: flex; align-items: center; gap: 14px;
  }
  .brand-dot {
    width: 34px; height: 34px; border-radius: 50%;
    background: var(--brand-blue);
  }
  .brand-name {
    font-weight: 700; color: var(--brand-blue);
    line-height: 1; letter-spacing: -0.5px;
  }

  /* back side */
  .card-back .brand { position: absolute; left: 70px; top: 110px; }
  .card-back .brand-name { font-size: 40px; }
  .card-back .website {
    position: absolute; left: 70px; top: 196px;
    color: var(--text-light); font-size: 14px; letter-spacing: 5px;
  }

  /* front side */
  .card-front .brand { position: absolute; right: 40px; top: 60px; }
  .card-front .brand-name { font-size: 34px; }
  .card-front .brand-dot { width: 28px; height: 28px; }
  .person {
    position: absolute; left: 40px; top: 178px; width: 150px; text-align: right;
  }
  .person-name { color: var(--text-light); font-size: 18px; font-weight: 700; }
  .person-role { color: var(--brand-blue); font-size: 15px; margin-top: 4px; }
  .divider {
    position: absolute; left: 210px; top: 170px;
    width: 1px; height: 120px; background: var(--divider);
  }
  .contact {
    position: absolute; left: 230px; top: 172px;
    list-style: none; color: var(--text-light); font-size: 15px; line-height: 1.45;
  }
  .contact li { display: flex; align-items: center; gap: 10px; }
  .contact .no-icon { padding-left: 0; }
  .contact svg { width: 16px; height: 16px; fill: var(--text-muted); flex: none; }
</style>
</head>
<body>
<main class="canvas">
  <section class="card card-back" aria-label="Card back">
    <div class="brand">
      <span class="brand-dot"></span>
      <span class="brand-name">Brightwave Digital</span>
    </div>
    <p class="website">www.brightwave.com</p>
  </section>

  <section class="card card-front" aria-label="Card front">
    <div class="brand">
      <span class="brand-dot"></span>
      <span class="brand-name">Brightwave Digital</span>
    </div>
    <div class="person">
      <p class="person-name">Mara Lindqvist</p>
      <p class="person-role">President</p>
    </div>
    <span class="divider"></span>
    <ul class="contact">
      <li class="no-icon">1427 Harbor View Lane</li>
      <li class="no-icon">Lakeside, NY 11020</li>
      <li>
        <svg viewBox="0 0 16 16" aria-label="Phone"><path d="M3 2h3l1 3-2 1a8 8 0 0 0 5 5l1-2 3 1v3c0 1-1 1-1 1C7 14 2 9 2 3c0 0 0-1 1-1z"/></svg>
        555 0142 7781
      </li>
      <li>
        <svg viewBox="0 0 16 16" aria-label="Fax"><path d="M4 1h7v4H4zM2 6h12v7H2zM5 9h6v1H5zM5 11h6v1H5z"/></svg>
        555 0193 2640
      </li>
      <li>
        <svg viewBox="0 0 16 16" aria-label="Email"><path d="M1 3h14v10H1zM2 4v1l6 4 6-4V4L8 8z" fill-rule="evenodd"/></svg>
        mara@brightwave.com
      </li>
    </ul>
  </section>
</main>
</body>
</html>
```